Local Flower Farm Needs Business Card Design

I need business cards designed for a flower farm based in Eudora, Kansas.
Business Info:
We are a local cut flower farm located in Eudora, Kansas, founded by Corinne Haldwick. What started as a passion for agriculture and search for more joy in daily life has blossomed into a small business dedicated to providing the community with beautiful, fresh, and sustainable flowers. We specialize in local, seasonal blooms, ensuring that every petal reflects the care and dedication we pour into our craft. Our mission is to deliver the highest quality flowers directly to our customers through local farmers markets and to florists who share our commitment to sustainability. Join us in celebrating the beauty of nature, one bloom at a time!
Contact Details:
Corinne Haldwick
Owner
Phone 913-555-0147
Facebook: Rosalind Thorpe Gardens
Instagram: @RosalindThorpeGardens
Website: RosalindThorpeGardens.example
Target Market(s)
Wholesale to Florists and Direct to Consumer via Farmers Market
Industry/Entity Type
Florist, Farm
Contact Information for Business Card
Name, Contact Info, Logo
Look and feel
Each slider illustrates characteristics of the customer's brand and the style your logo design should communicate.

```html
<!DOCTYPE html>
<html lang="en">
<head>
<meta charset="utf-8">
<title>Rosalind Thorpe Gardens – Business Card</title>
<link rel="stylesheet" href="https://fonts.googleapis.com/css2?family=EB+Garamond:wght@400;500;700&display=swap">
<style>
  :root {
    --ink: #0b2a2d;
    --paper: #ffffff;
    --mist: #c4c8ca;
    --stage: #e9eaea;
    --text: #1a1a1a;
  }
  * { margin: 0; padding: 0; box-sizing: border-box; }
  html, body { width: 1200px; height: 900px; overflow: hidden; }
  body {
    background: var(--stage);
    font-family: "EB Garamond", serif;
    position: relative;
  }
  .card {
    position: absolute;
    left: 290px;
    width: 620px;
    height: 354px;
    box-shadow: 0 6px 18px rgba(0,0,0,.18);
    overflow: hidden;
  }
  .card--front { top: 78px; background: var(--ink); }
  .card--back { top: 468px; background: var(--paper); }

  .brand-seal {
    position: absolute;
    border-radius: 50%;
    display: flex;
    align-items: center;
    justify-content: center;
    text-align: center;
    font-family: "EB Garamond", serif;
    font-weight: 500;
    letter-spacing: .14em;
    text-transform: uppercase;
  }
  .card--front .brand-seal {
    left: 210px; top: 77px; width: 200px; height: 200px;
    border: 1.5px solid var(--paper);
    color: var(--paper);
    font-size: 20px; line-height: 1.35;
  }
  .card--back .brand-seal {
    left: 378px; top: 38px; width: 184px; height: 184px;
    border: 1.5px solid var(--ink);
    color: var(--ink);
    font-size: 18px; line-height: 1.35;
    z-index: 2;
  }

  .wave { position: absolute; inset: 0; width: 100%; height: 100%; }

  .divider {
    position: absolute;
    left: 330px; top: 70px;
    width: 2px; height: 120px;
    background: var(--ink);
  }

  .contact {
    position: absolute;
    left: 44px; top: 98px;
    color: var(--text);
    z-index: 2;
  }
  .contact__name {
    font-weight: 700;
    font-size: 25px;
    color: var(--ink);
    line-height: 1.1;
  }
  .contact__role { font-size: 17px; margin: 2px 0 14px 12px; }
  .contact__list { list-style: none; }
  .contact__item {
    display: flex; align-items: center; gap: 6px;
    font-size: 17px; line-height: 1.45;
  }
  .contact__icon { width: 14px; height: 14px; flex: none; }
</style>
</head>
<body>

<section class="card card--front" aria-label="Card front">
  <div class="brand-seal">Rosalind<br>Thorpe<br>Gardens</div>
</section>

<section class="card card--back" aria-label="Card back">
  <svg class="wave" viewBox="0 0 620 354" preserveAspectRatio="none" aria-hidden="true">
    <path d="M620 150 C 560 240, 470 250, 360 280 C 260 305, 200 320, 150 354 L 620 354 Z" fill="#c4c8ca"/>
    <path d="M620 165 C 565 250, 475 262, 365 292 C 270 318, 215 332, 180 354 L 620 354 Z" fill="#ffffff"/>
    <path d="M620 175 C 570 265, 480 276, 370 306 C 290 328, 240 340, 215 354 L 620 354 Z" fill="#0b2a2d"/>
  </svg>

  <div class="divider"></div>
  <div class="brand-seal">Rosalind<br>Thorpe<br>Gardens</div>

  <div class="contact">
    <p class="contact__name">Corinne Haldwick</p>
    <p class="contact__role">Owner</p>
    <ul class="contact__list">
      <li class="contact__item">
        <svg class="contact__icon" viewBox="0 0 16 16"><path d="M3 2h3l1.5 3.5-2 1.3a8 8 0 0 0 3.7 3.7l1.3-2L14 10v3a1.5 1.5 0 0 1-1.5 1.5A11 11 0 0 1 1.5 3.5 1.5 1.5 0 0 1 3 2z" fill="#0b2a2d"/></svg>
        913-555-0147
      </li>
      <li class="contact__item">
        <svg class="contact__icon" viewBox="0 0 16 16"><circle cx="8" cy="8" r="6.5" fill="none" stroke="#0b2a2d" stroke-width="1.5"/><ellipse cx="8" cy="8" rx="2.8" ry="6.5" fill="none" stroke="#0b2a2d" stroke-width="1.2"/><line x1="1.5" y1="8" x2="14.5" y2="8" stroke="#0b2a2d" stroke-width="1.2"/></svg>
        RosalindThorpeGardens.example
      </li>
      <li class="contact__item">
        <svg class="contact__icon" viewBox="0 0 16 16"><rect x="1.5" y="1.5" width="13" height="13" rx="2" fill="#0b2a2d"/></svg>
        Rosalind Thorpe Gardens
      </li>
      <li class="contact__item">
        <svg class="contact__icon" viewBox="0 0 16 16"><rect x="1.5" y="1.5" width="13" height="13" rx="2" fill="#0b2a2d"/></svg>
        @RosalindThorpeGardens
      </li>
    </ul>
  </div>
</section>

</body>
</html>
```